Local Flower Farm Needs Business Card Design

I need business cards designed for a flower farm based in Eudora, Kansas.
Business Info:
We are a local cut flower farm located in Eudora, Kansas, founded by Corinne Haldwick. What started as a passion for agriculture and search for more joy in daily life has blossomed into a small business dedicated to providing the community with beautiful, fresh, and sustainable flowers. We specialize in local, seasonal blooms, ensuring that every petal reflects the care and dedication we pour into our craft. Our mission is to deliver the highest quality flowers directly to our customers through local farmers markets and to florists who share our commitment to sustainability. Join us in celebrating the beauty of nature, one bloom at a time!
Contact Details:
Corinne Haldwick
Owner
Phone 913-555-0147
Facebook: Rosalind Thorpe Gardens
Instagram: @RosalindThorpeGardens
Website: RosalindThorpeGardens.example
Target Market(s)
Wholesale to Florists and Direct to Consumer via Farmers Market
Industry/Entity Type
Florist, Farm
Contact Information for Business Card
Name, Contact Info, Logo
Look and feel
Each slider illustrates characteristics of the customer's brand and the style your logo design should communicate.

```html
<!DOCTYPE html>
<html lang="en">
<head>
<meta charset="utf-8">
<title>Rosalind Thorpe Gardens – Business Card</title>
<link rel="stylesheet" href="https://fonts.googleapis.com/css2?family=EB+Garamond:wght@400;600&display=swap">
<style>
  :root {
    --backdrop: #d6d7d7;
    --card-white: #ffffff;
    --forest: #0c2a2e;
    --arc-grey: #c9cccd;
    --ink-light: #ffffff;
    --ink-muted: #d8e2e2;
    --text-font: "EB Garamond", Georgia, serif;
  }
  * { box-sizing: border-box; margin: 0; padding: 0; }
  html, body { width: 1200px; height: 813px; overflow: hidden; }
  body {
    background: var(--backdrop);
    font-family: var(--text-font);
    position: relative;
  }
  .card {
    position: absolute;
    width: 525px;
    height: 300px;
    border-radius: 22px;
    overflow: hidden;
    background: var(--card-white);
    box-shadow: 0 6px 18px rgba(0,0,0,0.18);
  }
  .card-front { left: 50px; top: 256px; }
  .card-back  { left: 625px; top: 256px; }

  .brand {
    display: flex;
    align-items: center;
    gap: 10px;
    color: var(--forest);
    font-family: var(--text-font);
    font-weight: 400;
    letter-spacing: 0.06em;
    text-transform: uppercase;
  }
  .brand-dot {
    width: 14px; height: 14px;
    border-radius: 50%;
    background: var(--forest);
    flex: none;
  }
  .card-front .brand {
    position: absolute; inset: 0;
    justify-content: center;
    font-size: 26px;
  }

  .back-shape { position: absolute; inset: 0; }
  .card-back .brand {
    position: absolute;
    right: 28px; top: 70px;
    width: 200px;
    font-size: 19px;
    line-height: 1.2;
  }
  .contact {
    position: absolute;
    left: 30px; top: 145px;
    color: var(--ink-light);
  }
  .contact-name { font-size: 20px; font-weight: 600; }
  .contact-role { font-size: 14px; color: var(--ink-muted); margin-bottom: 12px; }
  .contact-list { list-style: none; font-size: 15px; line-height: 1.45; }
  .contact-list li { display: flex; align-items: center; gap: 7px; }
  .contact-list svg { width: 11px; height: 11px; flex: none; }
</style>
</head>
<body>

  <section class="card card-front" aria-label="Card front">
    <div class="brand"><span class="brand-dot"></span>Rosalind Thorpe Gardens</div>
  </section>

  <section class="card card-back" aria-label="Card back">
    <svg class="back-shape" viewBox="0 0 525 300" preserveAspectRatio="none" aria-hidden="true">
      <path d="M215 0 Q300 215 525 258 L525 276 Q290 240 200 0 Z" fill="var(--arc-grey)"/>
      <path d="M0 0 L200 0 Q290 240 525 276 L525 300 L0 300 Z" fill="var(--forest)"/>
    </svg>

    <div class="brand"><span class="brand-dot"></span>Rosalind Thorpe Gardens</div>

    <div class="contact">
      <p class="contact-name">Corinne Haldwick</p>
      <p class="contact-role">Owner</p>
      <ul class="contact-list">
        <li>
          <svg viewBox="0 0 12 12" aria-hidden="true"><path d="M2 1h2.5l1 3-1.5 1a7 7 0 0 0 3 3l1-1.5 3 1V10a1 1 0 0 1-1 1A9 9 0 0 1 1 2a1 1 0 0 1 1-1z" fill="#fff"/></svg>
          913-555-0147
        </li>
        <li>
          <svg viewBox="0 0 12 12" aria-hidden="true"><circle cx="6" cy="6" r="5" fill="none" stroke="#fff" stroke-width="1.2"/><path d="M1 6h10M6 1c-2.5 3-2.5 7 0 10M6 1c2.5 3 2.5 7 0 10" fill="none" stroke="#fff" stroke-width="0.9"/></svg>
          RosalindThorpeGardens.example
        </li>
        <li>
          <svg viewBox="0 0 12 12" aria-hidden="true"><rect x="1" y="1" width="10" height="10" fill="#fff"/></svg>
          Rosalind Thorpe Gardens
        </li>
        <li>
          <svg viewBox="0 0 12 12" aria-hidden="true"><rect x="1" y="1" width="10" height="10" fill="#fff"/></svg>
          @RosalindThorpeGardens
        </li>
      </ul>
    </div>
  </section>

</body>
</html>
```